Film Project Needs Investment Proposal

I'm trying to raise money to produce a feature film. I have the original mockup and the latest mockup uploaded to help show what I'm looking for. I've included the text and the images that should be used. Looking for a more professional and dynamic look to the pitch to project an impressive opportunity that can't refuse. Hopefully this will be fairly straightforward. I would love to have the elephant that was created as a iconic image to represent the movie. You can find that in the power point file. Thanks!
Updates

Project Deadline Extended Reason: By popular demand, designers have requested more time to submit for my project. Thanks! Added Saturday, February 18, 2017

Project Deadline Extended
Reason: Designers requested the deadline extension!

Industry/Entity Type

Investment

Requirements
Must have
• The text I have uploaded. It should follow the text. I have specific headers for each section of the text which I would like to see. These might be altered.
Nice to have
• Resemble the structure of the existing mockup brochures. 8-12 pages. Use the elephant logo that appears in the existing mockups-----a composite elephant image incorporating elements from the movie.
Should not have
• Cuts to the text.

```html
<!DOCTYPE html>
<html lang="en">
<head>
<meta charset="utf-8">
<title>The Edge of Cold Water – Script Development</title>
<link href="https://fonts.googleapis.com/css2?family=Montserrat:wght@300;400&display=swap" rel="stylesheet">
<style>
  :root {
    --backdrop: #9b9b9b;
    --ink-black: #070707;
    --caption-dark: #2a2a2a;
    --text-light: #e2e2e2;
    --text-muted: #a6a6a6;
    --sky: #d9dbdd;
    --sky-grey: #b4b6b8;
    --stone: #7a7364;
    --stone-dark: #3e3a33;
    --tree: #55565a;
    --snow: #eceef0;
    --asphalt: #2f3033;
    --portrait-warm: #9c8658;
    --portrait-olive: #6e6444;
    --portrait-skin: #b08a70;
    --portrait-shirt: #1c1c1e;
  }
  * { box-sizing: border-box; margin: 0; padding: 0; }
  html, body { width: 1200px; height: 1200px; overflow: hidden; }
  body {
    background: var(--backdrop);
    font-family: "Montserrat", sans-serif;
    font-weight: 300;
    position: relative;
  }
  .spread {
    position: absolute;
    left: 40px; top: 390px;
    width: 1120px; height: 420px;
    display: flex;
    box-shadow: 0 14px 30px rgba(0,0,0,0.25);
  }
  .intro-column {
    width: 215px;
    flex: none;
    background: var(--ink-black);
    color: var(--text-light);
    padding: 62px 20px 0 22px;
  }
  .section-heading {
    font-weight: 400;
    font-size: 10px;
    line-height: 1.2;
    text-transform: uppercase;
    letter-spacing: 0.01em;
    margin-bottom: 8px;
  }
  .section-body {
    font-size: 8.2px;
    line-height: 1.4;
    color: var(--text-muted);
  }
  .feature-photo {
    position: relative;
    width: 585px;
    flex: none;
    background:
      radial-gradient(ellipse 38% 30% at 78% 8%, var(--sky) 0%, rgba(217,219,221,0) 100%),
      radial-gradient(ellipse 30% 38% at 85% 40%, rgba(85,86,90,0.85) 0%, rgba(85,86,90,0) 100%),
      radial-gradient(ellipse 45% 32% at 40% 42%, rgba(122,115,100,0.95) 0%, rgba(122,115,100,0) 100%),
      radial-gradient(ellipse 40% 28% at 55% 62%, rgba(62,58,51,0.95) 0%, rgba(62,58,51,0) 100%),
      radial-gradient(ellipse 30% 30% at 88% 92%, var(--snow) 0%, rgba(236,238,240,0) 100%),
      radial-gradient(ellipse 50% 30% at 25% 90%, rgba(47,48,51,0.95) 0%, rgba(47,48,51,0) 100%),
      linear-gradient(180deg, var(--sky-grey) 0%, #8d8a83 30%, #5a5750 55%, #4a4b4e 75%, #8e9093 100%);
  }
  .feature-photo .title {
    position: absolute;
    left: 60px; bottom: 70px;
    color: #f4f4f4;
    font-weight: 300;
    font-size: 15px;
    letter-spacing: 0.02em;
    text-transform: uppercase;
  }
  .spine {
    position: absolute;
    left: 556px; top: 0;
    width: 22px; height: 100%;
    background: linear-gradient(90deg, rgba(0,0,0,0) 0%, rgba(0,0,0,0.3) 50%, rgba(255,255,255,0.08) 60%, rgba(0,0,0,0) 100%);
    pointer-events: none;
  }
  .profile-column {
    flex: 1;
    display: flex;
    flex-direction: column;
  }
  .profile-photo {
    height: 250px;
    background:
      radial-gradient(ellipse 26% 34% at 50% 44%, rgba(176,138,112,0.75) 0%, rgba(176,138,112,0) 100%),
      radial-gradient(ellipse 60% 30% at 55% 100%, var(--portrait-shirt) 0%, rgba(28,28,30,0) 100%),
      linear-gradient(90deg, var(--portrait-olive) 0%, var(--portrait-warm) 55%, #a8966d 100%);
  }
  .profile-caption {
    flex: 1;
    background: var(--caption-dark);
    color: var(--text-muted);
    padding: 14px 18px 0 22px;
  }
  .profile-name {
    font-weight: 300;
    font-size: 9.5px;
    color: var(--text-light);
    margin-bottom: 7px;
  }
  .profile-bio {
    font-size: 8.2px;
    line-height: 1.42;
  }
</style>
</head>
<body>
  <main class="spread">
    <section class="intro-column">
      <h2 class="section-heading">Script Development/Paper Kite Model</h2>
      <p class="section-body">The idea of shooting a movie in Wes's hometown with local actors, utilizing the unique, storied cultural history of the city of Ashford, began in 2003. Working with the Halvorsen Motion Picture Archive, Wes developed the idea of a heist movie, where a priceless film is stolen by a world class thief. Recently, table readings of the current script have been held in Ashford with local actors, along with a research scout to the Halvorsen House and local driving ranges. The recent success of his acclaimed short film PAPER KITE was rooted in a highly original story with a captivating central protagonist, who faces the deepest questions of life, capped off by an unforgettable ending. The idea is unique, wrapping classic noir elements of the femme fatale and a doomed hero with the new twist of heist movie involving film conservation and modern controversies around wildlife conservation and hunting.</p>
    </section>

    <figure class="feature-photo" role="img" aria-label="Photograph of a stone manor house with columned portico in winter, bare trees and snow along a curved driveway">
      <figcaption class="title">The Edge of Cold Water</figcaption>
    </figure>

    <section class="profile-column">
      <div class="profile-photo" role="img" aria-label="Portrait photograph of the writer-director in a dark shirt against a warm background"></div>
      <div class="profile-caption">
        <h3 class="profile-name">Wes Calloway</h3>
        <p class="profile-bio">Currently writing Adrian Vale's next movie for Nora Whitfield's Meridian Pictures, Wes Calloway has written award-winning feature and short films, distributed by Northlight Classics and screened at the Silverpine Film Festival. His recent short film PAPER KITE screened at over 50 festivals, bookended with winning the Harlan Reed Screenwriting award he won for STILL WATER at Silverpine. His next feature project will undoubtedly receive careful attention from the programmers at Silverpine who have received and supported his work for nearly 20 years, along with international distributors and audiences.</p>
      </div>
    </section>

    <div class="spine" aria-hidden="true"></div>
  </main>
</body>
</html>
```